New Dental Office Needs an Attractive and user friendly Website Designed

I need a website for a new dental office. The Name is Harrowfield Dentistry. I would like a Modern design with a user friendly interface and usability.
I would like a landing page, a page that lists the services we offer: Cosmetic Dentistry, Implants, Dental Hygiene, Emergency Services, Restorations, Dentures
Target Market(s)
Mid to upper class
Industry/Entity Type
Dentistry
Coding
Number of Pages Required
1 page
Requirements
Must have
- Landing page that has a scheduling option, Procedures, operating hours, and contact us info
Nice to have
- Appealing design, Soft comforting colors. Easy to navigate page, Modern and professional.

```html
<!DOCTYPE html>
<html lang="en">
<head>
<meta charset="utf-8">
<title>Harrowfield Dentistry</title>
<link href="https://fonts.googleapis.com/css2?family=Outfit:wght@300;400;500;600&display=swap" rel="stylesheet">
<style>
:root{
  --blue:#0a8fd6;
  --ink:#1d1d1f;
  --text:#3a3a3a;
  --muted:#8a8a8a;
  --header:#222222;
  --footer:#f2f2f2;
  --line:#e2e8ec;
  --white:#ffffff;
}
*{margin:0;padding:0;box-sizing:border-box}
html,body{width:1200px;height:2347px;overflow:hidden}
body{font-family:"Outfit",sans-serif;color:var(--text);background:var(--white);position:relative}
.abs{position:absolute}
a{color:inherit;text-decoration:none}

/* header */
.site-header{left:0;top:0;width:1200px;height:112px;background:var(--header)}
.topbar{left:355px;top:0;width:845px;height:38px;background:var(--blue);clip-path:polygon(0 0,100% 0,100% 100%,22px 100%)}
.topbar ul{list-style:none;display:flex;gap:42px;padding-left:53px;height:38px;align-items:center;font-size:11px;color:var(--white);text-transform:uppercase}
.topbar li{display:flex;align-items:center;gap:10px}
.topbar .ico{width:22px;height:20px;background:rgba(255,255,255,.2);border-radius:3px;display:flex;align-items:center;justify-content:center}
.brand{left:112px;top:24px;color:var(--white);font-size:26px;font-weight:500;line-height:1.05;width:200px;text-align:center}
.brand small{display:block;font-size:14px;letter-spacing:5px;margin-top:2px}
.main-nav{left:421px;top:64px;display:flex;gap:35px;font-size:13.5px;font-weight:500;color:var(--white);text-transform:uppercase}
.main-nav .active{color:var(--blue)}
.btn{display:inline-flex;align-items:center;justify-content:center;background:var(--blue);color:var(--white);border-radius:22px;font-weight:500;text-transform:uppercase}
.btn-schedule{left:936px;top:58px;width:186px;height:33px;font-size:12px}

/* hero */
.hero-media{left:0;top:112px;width:1200px;height:515px;background:linear-gradient(90deg,#eceeef 0%,#e4e7ea 45%,#cfd8de 70%,#bfc9d0 100%)}
.hero-title{left:110px;top:206px;font-size:32px;font-weight:600;color:var(--ink);letter-spacing:-.5px}
.hero-title span{background:var(--blue);color:var(--white);padding:0 4px}
.hero-text{left:111px;top:274px;width:495px;font-size:14.5px;line-height:35px;color:var(--text)}
.btn-start{left:111px;top:441px;width:179px;height:42px;font-size:14px}

.features{left:338px;top:557px;width:862px;height:141px;background:var(--blue);display:flex;color:var(--white)}
.feature{flex:1;display:flex;gap:14px;padding:30px 0 0 28px;border-right:1px solid rgba(255,255,255,.25)}
.feature:last-child{border-right:0}
.feature h3{font-size:18px;font-weight:500;line-height:31px;text-transform:uppercase}
.feature p{font-size:13px;line-height:26px;margin-top:3px}

/* procedures */
.section-title{font-size:30px;font-weight:600;color:var(--ink);display:flex;align-items:center;gap:18px;text-transform:uppercase;letter-spacing:-.5px}
.section-title i{display:block;width:38px;height:2px;background:var(--blue)}
.proc-title{left:0;width:1200px;top:770px;justify-content:center}
.proc-lead{left:245px;top:828px;width:710px;text-align:center;font-size:15.5px;line-height:33px;color:var(--muted)}
.card{top:957px;width:306px;height:266px;border:1px solid var(--line);border-radius:8px;background:var(--white);text-align:center;box-shadow:0 2px 8px rgba(0,0,0,.04)}
.card .badge{position:absolute;left:113px;top:-37px;width:80px;height:80px;border-radius:50%;background:var(--blue);display:flex;align-items:center;justify-content:center}
.card h3{margin-top:72px;font-size:19px;font-weight:500;color:var(--ink);text-transform:uppercase}
.card p{margin:16px 14px 0;font-size:15.5px;line-height:33.5px;color:var(--muted)}
.arrow{top:1075px;width:31px;height:31px;border-radius:50%;display:flex;align-items:center;justify-content:center}
.arrow-prev{left:35px;border:1.5px solid #333}
.arrow-next{left:1125px;border:1.5px solid var(--blue)}

/* about */
.about{left:0;top:1308px;width:1200px;height:605px;background:linear-gradient(180deg,#d6ecf9 0%,#f3f8fb 100%)}
.about-photo{left:112px;top:1378px;width:451px;height:449px;border-bottom-left-radius:240px;background:linear-gradient(135deg,#e9ecee,#cfd6dc 60%,#bcc7d0)}
.about-inset{left:395px;top:1628px;width:198px;height:198px;border-radius:50%;border:8px solid var(--white);background:linear-gradient(135deg,#8fa5b8,#3b5570)}
.about-title{left:661px;top:1393px}
.about-text{left:661px;top:1448px;width:432px;font-size:14.5px;line-height:34px;color:var(--text)}
.about-text p+p{margin-top:11px}
.btn-learn{left:661px;top:1759px;width:135px;height:42px;font-size:14px}

/* footer */
.site-footer{left:0;top:1913px;width:1200px;height:434px;background:var(--footer)}
.foot-h{font-size:21px;font-weight:500;color:var(--ink);text-transform:uppercase}
.foot-h::after{content:"";display:block;width:38px;height:2px;background:var(--blue);margin-top:10px}
.hours{left:94px;top:1992px}
.hours table{margin-top:20px;border-collapse:collapse;font-size:13px;color:var(--ink);text-transform:uppercase}
.hours td{height:33.5px;padding:0}
.hours td:first-child{width:105px}
.vline{top:1998px;width:1px;height:282px;background:#dcdcdc}
.foot-brand{left:420px;top:2022px;width:300px;text-align:center;color:var(--ink);font-size:36px;font-weight:500;line-height:1.05}
.foot-brand small{display:block;font-size:18px;letter-spacing:7px;margin-top:4px}
.foot-about{left:428px;top:2117px;width:284px;text-align:center;font-size:12.5px;line-height:30px;color:var(--ink)}
.contact{left:813px;top:1992px}
.contact ul{list-style:none;margin-top:26px}
.contact li{display:flex;gap:15px;font-size:13px;color:var(--ink);text-transform:uppercase;line-height:30px;margin-bottom:22px}
.contact .ico{flex:none;width:27px;height:27px;background:var(--blue);display:flex;align-items:center;justify-content:center}
.copyright{left:82px;top:2301px;width:1036px;display:flex;align-items:center;gap:12px;font-size:13px;color:var(--ink)}
.copyright i{flex:1;height:1px;background:#dcdcdc}
</style>
</head>
<body>

<header class="site-header abs">
  <div class="topbar abs">
    <ul>
      <li><span class="ico"><svg width="10" height="10" viewBox="0 0 24 24" fill="#fff"><path d="M6.6 10.8a15 15 0 0 0 6.6 6.6l2.2-2.2c.3-.3.7-.4 1-.2 1.1.4 2.3.6 3.6.6.6 0 1 .4 1 1V20c0 .6-.4 1-1 1C10.6 21 3 13.4 3 4c0-.6.4-1 1-1h3.5c.6 0 1 .4 1 1 0 1.3.2 2.5.6 3.6.1.3 0 .7-.2 1z"/></svg></span>+1 555 014 2280</li>
      <li><span class="ico"><svg width="10" height="8" viewBox="0 0 24 18" fill="#fff"><path d="M0 0h24v18H0z" opacity=".9"/><path d="M0 0l12 9 12-9" stroke="#0a8fd6" stroke-width="2" fill="none"/></svg></span>hello@harrowfielddental.example</li>
      <li><span class="ico"><svg width="10" height="8" viewBox="0 0 24 18" fill="#fff"><path d="M0 0h24v18H0z" opacity=".9"/><path d="M0 0l12 9 12-9" stroke="#0a8fd6" stroke-width="2" fill="none"/></svg></span>48 Harrowfield Lane Oakridge, TX 75012</li>
    </ul>
  </div>
  <div class="brand abs">Harrowfield<small>DENTISTRY</small></div>
  <nav class="main-nav abs">
    <a class="active" href="#">Home</a><a href="#">About Us</a><a href="#">Services</a><a href="#">New Patients</a><a href="#">Contact</a>
  </nav>
  <a class="btn btn-schedule abs" href="#">Schedule Appointment</a>
</header>

<section>
  <div class="hero-media abs" role="img" aria-label="Smiling patient seated in a bright modern dental treatment room"></div>
  <h1 class="hero-title abs">MODERN CARE, <span>TIMELESS</span> SMILES</h1>
  <p class="hero-text abs">Lorem ipsum dolor sit amet, consectetur adipiscing elit, sed do eiusmod tempor incididunt ut labore et dolore magna aliqua. Ut enim ad minim veniam, quis nostrud exercitation ullamco laboris nisi ut aliquip ex ea commodo consequat.</p>
  <a class="btn btn-start abs" href="#">Get Started Now</a>

  <div class="features abs">
    <div class="feature">
      <svg width="38" height="38" viewBox="0 0 38 38" fill="none" stroke="#fff" stroke-width="1.5"><path d="M4 24h8l6 4h10v4H10l-6-3z"/><path d="M14 20c-4-3-6-6-6-9a5 5 0 0 1 9-3 5 5 0 0 1 9 3c0 3-2 6-6 9"/><path d="M10 13h4l2-3 3 6 2-3h4"/><circle cx="30" cy="7" r="4"/></svg>
      <div><h3>Advanced Care</h3><p>Lorem ipsum dolor sit amet<br>consectetur adipiscing</p></div>
    </div>
    <div class="feature">
      <svg width="38" height="38" viewBox="0 0 38 38" fill="none" stroke="#fff" stroke-width="1.5"><rect x="3" y="6" width="28" height="24" rx="2"/><path d="M3 12h28M9 3v6M25 3v6"/><path d="M8 17h3M14 17h3M20 17h3M8 22h3M14 22h3"/><circle cx="29" cy="29" r="6" fill="#0a8fd6"/><path d="M26 29l2 2 4-4"/></svg>
      <div><h3>Same-Day<br>Appointments</h3><p>Lorem ipsum dolor sit amet</p></div>
    </div>
    <div class="feature">
      <svg width="38" height="38" viewBox="0 0 38 38" fill="none" stroke="#fff" stroke-width="1.5"><circle cx="12" cy="9" r="4"/><circle cx="26" cy="9" r="4"/><path d="M5 22c0-5 3-8 7-8s7 3 7 8M19 22c0-5 3-8 7-8s7 3 7 8"/><path d="M10 26l6 6 4-2 8-8"/></svg>
      <div><h3>Family Friendly</h3><p>Lorem ipsum dolor sit amet<br>consectetur adipiscing</p></div>
    </div>
  </div>
</section>

<section>
  <h2 class="section-title proc-title abs"><i></i>Our Procedures<i></i></h2>
  <p class="proc-lead abs">At Harrowfield Dentistry, we offer a full range of modern dental treatments designed to improve your health, comfort, and confidence.</p>

  <a class="arrow arrow-prev abs" href="#" aria-label="Previous"><svg width="10" height="12" viewBox="0 0 10 12"><path d="M7 1L2 6l5 5" stroke="#333" stroke-width="1.5" fill="none"/></svg></a>

  <article class="card abs" style="left:111px">
    <div class="badge"><svg width="46" height="46" viewBox="0 0 46 46" fill="none" stroke="#fff" stroke-width="1.6"><path d="M9 20c0-9 6-14 13-14s13 5 13 14c0 9-6 17-13 17S9 29 9 20z"/><circle cx="17" cy="19" r="2.5"/><circle cx="27" cy="19" r="2.5"/><path d="M18 28h8"/><rect x="27" y="28" width="12" height="12" rx="1"/><path d="M30 32h6M30 36h6"/></svg></div>
    <h3>Cosmetic Dentistry</h3>
    <p>Enhance your smile with whitening, veneers, bonding, and more. Whether you're looking for subtle improvements or a full smile</p>
  </article>
  <article class="card abs" style="left:447px">
    <div class="badge"><svg width="46" height="46" viewBox="0 0 46 46" fill="none" stroke="#fff" stroke-width="1.6"><path d="M25 5h10l-1 7h-8z"/><path d="M30 12v8"/><path d="M8 22c0-4 3-5 6-4l3 1 3-1c3-1 6 0 6 4 0 3-1 5-2 7l-1 10h-3l-2-7-2 7h-3l-1-10c-1-2-4-4-4-7z"/><path d="M20 36c4 2 10 2 16 0M36 24v10"/></svg></div>
    <h3>Dental Implants</h3>
    <p>Missing a tooth? Implants offer a permanent, secure, and natural looking replacement that helps preserve bone and restore function</p>
  </article>
  <article class="card abs" style="left:783px">
    <div class="badge"><svg width="46" height="46" viewBox="0 0 46 46" fill="none" stroke="#fff" stroke-width="1.6"><path d="M11 17c0-5 4-7 8-6l4 1 4-1c4-1 8 1 8 6 0 4-2 7-3 10l-1 11h-4l-3-9-3 9h-4l-1-11c-1-3-5-6-5-10z"/><path d="M13 20h20M8 8l3 3M38 8l-3 3M23 4v4"/></svg></div>
    <h3>Dental Hygiene</h3>
    <p>Preventive care is the foundation of lasting oral health. Our dental cleanings and exams help catch issues early and keep your teeth</p>
  </article>

  <a class="arrow arrow-next abs" href="#" aria-label="Next"><svg width="10" height="12" viewBox="0 0 10 12"><path d="M3 1l5 5-5 5" stroke="#0a8fd6" stroke-width="1.5" fill="none"/></svg></a>
</section>

<section>
  <div class="about abs"></div>
  <div class="about-photo abs" role="img" aria-label="Dental team of three in white coats reviewing patient notes together"></div>
  <div class="about-inset abs" role="img" aria-label="Patient receiving a teeth whitening light treatment"></div>
  <h2 class="section-title about-title abs">About Harrowfield<i></i></h2>
  <div class="about-text abs">
    <p>At Harrowfield Dentistry, we believe a great smile starts with trust, comfort, and care you can count on. Our mission is to provide modern, high-quality dental care in a calm, welcoming environment—where you're treated like family, not just a patient.</p>
    <p>Whether you're here for a routine check-up or a full smile restoration, we're committed to helping you achieve long-term oral health and the confidence that comes with it.</p>
  </div>
  <a class="btn btn-learn abs" href="#">Learn More</a>
</section>

<footer class="site-footer abs"></footer>
<div class="hours abs">
  <h4 class="foot-h">Operating Hours</h4>
  <table>
    <tr><td>Monday</td><td>8:00 AM – 6:00 PM</td></tr>
    <tr><td>Tuesday</td><td>8:00 AM – 6:00 PM</td></tr>
    <tr><td>Wednesday</td><td>8:00 AM – 6:00 PM</td></tr>
    <tr><td>Thursday</td><td>8:00 AM – 6:00 PM</td></tr>
    <tr><td>Friday</td><td>8:00 AM – 4:00 PM</td></tr>
    <tr><td>Saturday</td><td>9:00 AM – 1:00 PM</td></tr>
    <tr><td>Sunday</td><td>Closed</td></tr>
  </table>
</div>
<div class="vline abs" style="left:379px"></div>
<div class="foot-brand abs">Harrowfield<small>DENTISTRY</small></div>
<p class="foot-about abs">We take the time to get to know you, explain your options, and work with you to create a treatment plan that fits your needs, goals, and budget.</p>
<div class="vline abs" style="left:763px"></div>
<div class="contact abs">
  <h4 class="foot-h">Contact Us</h4>
  <ul>
    <li><span class="ico"><svg width="12" height="12" viewBox="0 0 24 24" fill="#fff"><path d="M6.6 10.8a15 15 0 0 0 6.6 6.6l2.2-2.2c.3-.3.7-.4 1-.2 1.1.4 2.3.6 3.6.6.6 0 1 .4 1 1V20c0 .6-.4 1-1 1C10.6 21 3 13.4 3 4c0-.6.4-1 1-1h3.5c.6 0 1 .4 1 1 0 1.3.2 2.5.6 3.6.1.3 0 .7-.2 1z"/></svg></span>+1 555 014 2280</li>
    <li><span class="ico"><svg width="12" height="9" viewBox="0 0 24 18"><path d="M0 0h24v18H0z" fill="#fff"/><path d="M0 0l12 9 12-9" stroke="#0a8fd6" stroke-width="2" fill="none"/></svg></span>hello@harrowfielddental.example</li>
    <li><span class="ico"><svg width="12" height="9" viewBox="0 0 24 18"><path d="M0 0h24v18H0z" fill="#fff"/><path d="M0 0l12 9 12-9" stroke="#0a8fd6" stroke-width="2" fill="none"/></svg></span>48 Harrowfield Lane Oakridge,<br>TX 75012</li>
  </ul>
</div>
<div class="copyright abs"><i></i>COPYRIGHT © 2025 HARROWFIELD DENTISTRY | ALL RIGHTS RESERVED<i></i></div>

</body>
</html>
```